Website Design Project for Beauty & Wellness Professionals

As background information, I have a website that is focused on Beauty & Wellness Professionals:
- Job Search (www.lumarinovo.com)
- Business Classifieds (negocios.lumarinovo.com)
- Freelancer Classifieds (freelancer.lumarinovo.com)
- Course Reviews (cursos.lumarinovo.com)

All those websites use standard templates.

I need a DESIGN for the HOME PAGE (no coding) of the Website Platform that consolidates the four platforms under the same design.

Website designs that we like:
- quelvox.com
- brintmoor.com

Target Market(s)

Brazilian Professionals from Beauty & Wellness sector

Industry/Entity Type

Business

Requirements
Must have
• Website designs that we like:
- quelvox.com
- brintmoor.com

```html
<!DOCTYPE html>
<html lang="pt-BR">
<head>
<meta charset="utf-8">
<title>Lumarinovo Beauty</title>
<link href="https://fonts.googleapis.com/css2?family=Source+Sans+3:wght@400;600;700&display=swap" rel="stylesheet">
<style>
:root{
  --teal:#3d9fc0;
  --teal-light:#7fcbd9;
  --teal-deep:#2f7f9c;
  --orange:#d8672e;
  --green:#4c9e45;
  --green-btn:#76b55a;
  --salmon:#e39b73;
  --sky-btn:#6cc0dc;
  --ink:#444;
  --muted:#888;
  --panel:#efefef;
  --white:#fff;
  --footer-top:#86cfdc;
  --footer-mid:#4aa2bf;
  --footer-bottom:#2f88a8;
}
*{box-sizing:border-box;margin:0;padding:0}
html,body{width:1200px;height:2284px;overflow:hidden;background:#fff}
body{font-family:"Source Sans 3",sans-serif;color:var(--ink);position:relative}
.abs{position:absolute}
a{color:inherit;text-decoration:none}

/* header */
.site-header{position:absolute;left:0;top:0;width:1200px;height:165px;background:#fff}
.brand{position:absolute;left:118px;top:60px;display:flex;align-items:center;gap:12px;color:var(--teal);font-size:32px;font-weight:400}
.brand-dot{width:22px;height:22px;border-radius:50%;background:var(--teal)}
.top-actions{position:absolute;top:24px;left:731px;display:flex;gap:6px}
.btn-top{height:31px;border-radius:4px;color:#fff;font-size:13px;display:flex;align-items:center;justify-content:center;text-transform:none}
.btn-advertise{width:175px;background:var(--sky-btn)}
.btn-login{width:65px;background:var(--green-btn)}
.btn-register{width:86px;background:var(--salmon)}
.main-nav{position:absolute;top:120px;left:419px;display:flex;gap:22px;font-size:15px;color:#555}
.main-nav .active{color:var(--orange)}

/* hero */
.hero{position:absolute;left:0;top:165px;width:1200px;height:525px;background:linear-gradient(100deg,#6b4a3c 0%,#c99a86 30%,#d9c7b3 55%,#a7b8a4 80%,#8a9e8a 100%)}
.hero-dots{position:absolute;left:1049px;top:208px;display:flex;flex-direction:column;gap:10px}
.hero-dots span{width:11px;height:11px;border-radius:50%;background:#8fd2e6}
.hero-dots span:last-child{background:#fff}
.hero-title{position:absolute;left:0;width:1200px;top:475px;text-align:center;color:#fff;font-size:31px;font-weight:600;text-shadow:0 1px 3px rgba(0,0,0,.5)}
.hero-sub{position:absolute;left:0;width:1200px;top:518px;text-align:center;color:#fff;font-size:16px;font-weight:600;text-shadow:0 1px 2px rgba(0,0,0,.5)}
.search-bar{position:absolute;left:157px;top:555px;width:888px;height:52px;background:rgba(60,60,60,.55);border-radius:4px}
.field{position:absolute;top:6px;height:36px;background:#fff;border-radius:2px;font-size:13px;color:#888;display:flex;align-items:center;padding-left:16px}
.field svg{position:absolute;right:12px;top:14px}
.f-query{left:4px;width:320px}
.f-cat{left:329px;width:225px}
.f-by{left:560px;width:227px}
.btn-search{position:absolute;left:792px;top:6px;width:93px;height:36px;background:var(--sky-btn);border-radius:2px;color:#fff;font-size:15px;font-weight:600;display:flex;align-items:center;justify-content:center}

/* featured */
.section-title{position:absolute;left:0;width:1200px;top:710px;text-align:center;color:var(--green);font-size:34px;font-weight:600}
.job-card{position:absolute;width:315px;height:195px;color:#fff;text-align:center}
.job-card .job-title{position:absolute;left:0;width:100%;top:72px;font-size:33px;font-weight:600;text-shadow:0 1px 3px rgba(0,0,0,.6)}
.job-card .job-meta{position:absolute;left:0;width:100%;top:121px;font-size:13px;text-shadow:0 1px 2px rgba(0,0,0,.6)}
.tone-a{background:linear-gradient(135deg,#4a3a33,#2a2523)}
.tone-b{background:linear-gradient(135deg,#3a2a28,#5a3a34)}
.tone-c{background:linear-gradient(135deg,#2f4a4e,#1e3234)}
.tone-d{background:linear-gradient(135deg,#7c6a5c,#b39a86)}
.tone-e{background:linear-gradient(135deg,#6a5a48,#8a7a68)}
.tone-f{background:linear-gradient(135deg,#7a3a44,#a55a5e)}
.tone-g{background:linear-gradient(135deg,#7a5a50,#a58478)}
.tone-h{background:linear-gradient(135deg,#3a2838,#5a3a50)}
.tone-i{background:linear-gradient(135deg,#8a7a70,#c4b2a2)}

/* info boxes */
.info-box{position:absolute;top:1436px;width:315px;height:195px;background:linear-gradient(#f3f3f3,#e8e8e8);text-align:center}
.info-box h3{margin-top:20px;font-size:26px;font-weight:600}
.email-box h3{color:var(--green)}
.vacancy-box h3{color:var(--orange)}
.course-box h3{color:var(--teal)}
.email-input{position:absolute;left:32px;top:74px;width:256px;height:40px;background:#fff;border-radius:4px;box-shadow:0 1px 3px rgba(0,0,0,.15);font-size:13px;color:#aaa;display:flex;align-items:center;padding-left:44px}
.email-input svg{position:absolute;left:12px;top:13px}
.btn-subscribe{position:absolute;left:94px;top:130px;width:108px;height:32px;background:var(--green-btn);color:#fff;font-size:16px;display:flex;align-items:center;padding-left:12px;clip-path:polygon(0 0,86% 0,100% 50%,86% 100%,0 100%);border-radius:4px 0 0 4px}
.vacancy-list{position:absolute;left:26px;top:80px;display:grid;grid-template-columns:145px 130px;row-gap:8px;text-align:left;font-size:13px;color:#777;list-style:none}
.vacancy-list li::before{content:"• ";color:#999}
.course-text{position:absolute;left:26px;top:70px;width:263px;text-align:justify;font-size:13px;line-height:26px;color:#777}
.course-badge{position:absolute;right:28px;bottom:20px;font-size:14px;font-weight:600;color:#555;display:flex;align-items:center;gap:4px}
.course-badge span{width:16px;height:16px;background:var(--orange)}

/* footer */
.footer-links{position:absolute;left:0;top:1654px;width:1200px;height:336px;background:linear-gradient(var(--footer-top),var(--footer-mid));border-top:2px solid #a9dfe8}
.footer-heading{position:absolute;left:143px;top:28px;font-size:19px;color:#fff}
.link-col{position:absolute;width:110px;color:#fff}
.link-col h4{font-size:14px;font-weight:400;margin-bottom:10px;color:#f2fbfd}
.link-col li{list-style:none;font-size:12px;line-height:24px}
.link-col li::before{content:"";display:inline-block;border-left:5px solid #fff;border-top:3px solid transparent;border-bottom:3px solid transparent;margin-right:6px}
.tag-panel{position:absolute;left:615px;top:23px;width:463px;height:282px;background:#fff;box-shadow:0 1px 4px rgba(0,0,0,.2)}
.tag-input{position:absolute;left:55px;top:30px;width:230px;height:28px;border:1px solid #ddd;border-radius:3px;background:linear-gradient(#f2f2f2,#fff)}
.btn-tag{position:absolute;left:292px;top:31px;width:86px;height:26px;background:var(--teal-deep);color:#fff;font-size:11px;border-radius:3px;display:flex;align-items:center;justify-content:center}
.tags{position:absolute;left:55px;top:78px;width:360px;display:flex;flex-wrap:wrap;gap:11px 8px}
.tag{height:25px;padding:0 12px;border:1px solid #e2e2e2;border-radius:3px;font-size:13px;color:#555;display:flex;align-items:center}
.footer-social{position:absolute;left:0;top:1990px;width:1200px;height:235px;background:linear-gradient(var(--footer-mid),var(--footer-bottom));border-top:1px solid #6fbad0}
.footer-social h4{position:absolute;top:40px;font-size:19px;font-weight:400;color:#fff}
.feed-grid{position:absolute;left:155px;top:68px;width:245px;height:140px;background:#fff;padding:6px;display:grid;grid-template-columns:repeat(4,1fr);gap:8px 10px;align-content:start}
.feed-grid .thumb{height:50px;background:linear-gradient(135deg,#9a8a80,#4a423e)}
.feed-grid small{position:absolute;left:6px;bottom:3px;font-size:10px;color:#999}
.tweet-bubble{position:absolute;left:480px;top:75px;width:230px;height:116px;background:rgba(255,255,255,.2);border-radius:8px;padding:16px 20px;color:#fff;font-size:12px;line-height:20px}
.tweet-dot{position:absolute;left:635px;top:30px;width:36px;height:36px;border-radius:50%;background:#4aa8e0}
.follow-list{position:absolute;left:769px;top:84px;list-style:none}
.follow-list li{display:flex;align-items:center;gap:16px;height:30px;margin-bottom:10px;color:#fff;font-size:14px}
.follow-list span{width:30px;height:30px;border-radius:2px}
.sq-chirp{background:#37a8df}
.sq-rss{background:#f08a1c}
.sq-mural{background:#2d5ea6}
.sq-orbe{background:#444}
.copyright{position:absolute;left:0;top:2225px;width:1200px;height:59px;background:#2e86a6;color:#fff;font-size:14px;display:flex;align-items:center;justify-content:center;gap:8px}
</style>
</head>
<body>

<header class="site-header">
  <div class="brand"><span class="brand-dot"></span>Lumarinovo Beauty</div>
  <div class="top-actions">
    <a class="btn-top btn-advertise">Advertise JOB VACANCY</a>
    <a class="btn-top btn-login">LOG IN</a>
    <a class="btn-top btn-register">REGISTER</a>
  </div>
  <nav class="main-nav">
    <a class="active">FOR PROFESSIONALS</a>
    <a>FOR BUSINESS</a>
    <a>EVENTS &amp; PARTNERS</a>
    <a>ABOUT US</a>
    <a>BLOG</a>
    <a>CONTACT US</a>
  </nav>
</header>

<section class="hero" role="img" aria-label="Hero photo of a smiling young woman in a floral dress"></section>
<div class="hero-dots"><span></span><span></span><span></span><span></span></div>
<h1 class="hero-title">Local Job Search and desired!</h1>
<p class="hero-sub">Ex: Manicure São Paulo, Rio de Janeiro Hairdresser</p>
<form class="search-bar">
  <div class="field f-query">Escreva aqui profissao e Local</div>
  <div class="field f-cat">Vagas Beleza<svg width="10" height="6"><path d="M0 0h10L5 6z" fill="#999"/></svg></div>
  <div class="field f-by">Buscar por<svg width="10" height="6"><path d="M0 0h10L5 6z" fill="#999"/></svg></div>
  <div class="btn-search">SEARCH</div>
</form>

<h2 class="section-title">Featured Job Vacancies</h2>

<article class="job-card tone-a" style="left:104px;top:769px" role="img" aria-label="Photo of a hairdresser styling hair"><div class="job-title">Hair dressing job</div><div class="job-meta">Ex: Manicure São Paulo, Rio de Janeiro Hairdresser</div></article>
<article class="job-card tone-b" style="left:445px;top:769px" role="img" aria-label="Photo of a pedicure with flower petals"><div class="job-title">Beauty job</div><div class="job-meta">Ex: Manicure São Paulo, Rio de Janeiro Hairdresser</div></article>
<article class="job-card tone-c" style="left:786px;top:769px" role="img" aria-label="Photo of a fashion model"><div class="job-title">Fashion job</div><div class="job-meta">Ex: Manicure São Paulo, Rio de Janeiro Hairdresser</div></article>

<article class="job-card tone-d" style="left:104px;top:991px" role="img" aria-label="Photo of a facial massage"><div class="job-title">Job Title</div><div class="job-meta">Ex: Manicure São Paulo, Rio de Janeiro Hairdresser</div></article>
<article class="job-card tone-e" style="left:445px;top:991px" role="img" aria-label="Photo of spa towels and orchids"><div class="job-title">Job Title</div><div class="job-meta">Ex: Manicure São Paulo, Rio de Janeiro Hairdresser</div></article>
<article class="job-card tone-f" style="left:786px;top:991px" role="img" aria-label="Photo of a woman with a red flower"><div class="job-title">Job Title</div><div class="job-meta">Ex: Manicure São Paulo, Rio de Janeiro Hairdresser</div></article>

<article class="job-card tone-g" style="left:104px;top:1214px" role="img" aria-label="Photo of a spa treatment"><div class="job-title">Job Title</div><div class="job-meta">Ex: Manicure São Paulo, Rio de Janeiro Hairdresser</div></article>
<article class="job-card tone-h" style="left:445px;top:1214px" role="img" aria-label="Photo of makeup application"><div class="job-title">Job Title</div><div class="job-meta">Ex: Manicure São Paulo, Rio de Janeiro Hairdresser</div></article>
<article class="job-card tone-i" style="left:786px;top:1214px" role="img" aria-label="Photo of a woman beside white roses"><div class="job-title">Job Title</div><div class="job-meta">Ex: Manicure São Paulo, Rio de Janeiro Hairdresser</div></article>

<section class="info-box email-box" style="left:104px">
  <h3>Assinar por Email</h3>
  <div class="email-input"><svg width="22" height="15"><rect x="0.5" y="0.5" width="21" height="14" fill="none" stroke="#ccc"/><path d="M1 1l10 7 10-7" fill="none" stroke="#ccc"/></svg>Enter your Email</div>
  <div class="btn-subscribe">Subscribe</div>
</section>
<section class="info-box vacancy-box" style="left:445px">
  <h3>Job Vacancy</h3>
  <ul class="vacancy-list">
    <li>Assistant Hairdresser</li><li>Designer Eyebrow</li>
    <li>Assistant Cleaning</li><li>Featured</li>
    <li>Hairdresser</li><li>Nurse</li>
  </ul>
</section>
<section class="info-box course-box" style="left:786px">
  <h3>Online Courses Cursiva</h3>
  <p class="course-text">Lorem ipsum dolor sit amet, consectetur adipisicing elit, sed do eiusmod tempor incididunt ut labore et dolore magna aliqua.</p>
  <div class="course-badge">cursiva<span></span></div>
</section>

<footer>
  <div class="footer-links">
    <div class="footer-heading">Footer</div>
    <div class="link-col" style="left:145px;top:68px"><h4>Titile Link</h4><ul><li>Subtitle Link</li><li>Subtitle Link</li><li>Subtitle Link</li></ul></div>
    <div class="link-col" style="left:254px;top:68px"><h4>Title Link</h4><ul><li>Subtitle Link</li><li>Subtitle Link</li><li>Subtitle Link</li></ul></div>
    <div class="link-col" style="left:366px;top:68px"><h4>Title Link</h4><ul><li>Subtitle Link</li><li>Subtitle Link</li><li>Subtitle Link</li></ul></div>
    <div class="link-col" style="left:477px;top:68px"><h4>Title Link</h4><ul><li>Subtitle Link</li><li>Subtitle Link</li><li>Subtitle Link</li></ul></div>
    <div class="link-col" style="left:145px;top:200px"><h4>Titile Link</h4><ul><li>Subtitle Link</li><li>Subtitle Link</li><li>Subtitle Link</li></ul></div>
    <div class="link-col" style="left:254px;top:200px"><h4>Title Link</h4><ul><li>Subtitle Link</li><li>Subtitle Link</li><li>Subtitle Link</li></ul></div>
    <div class="link-col" style="left:366px;top:200px"><h4>Title Link</h4><ul><li>Subtitle Link</li><li>Subtitle Link</li><li>Subtitle Link</li></ul></div>
    <div class="link-col" style="left:477px;top:200px"><h4>Title Link</h4><ul><li>Subtitle Link</li><li>Subtitle Link</li><li>Subtitle Link</li></ul></div>

    <div class="tag-panel">
      <div class="tag-input"></div>
      <div class="btn-tag">+ Add Tag</div>
      <div class="tags">
        <span class="tag">Yellow</span><span class="tag">Pressly theme</span><span class="tag">User interface</span>
        <span class="tag">Light</span><span class="tag">Dark</span><span class="tag">Button</span><span class="tag">Brown</span><span class="tag">Blue</span>
        <span class="tag">Breadcrumbs</span><span class="tag">Subscribe</span><span class="tag">Form</span><span class="tag">Post</span>
        <span class="tag">Orbe</span><span class="tag">Green</span><span class="tag">Menu</span><span class="tag">Portfolio</span>
        <span class="tag">Metal</span><span class="tag">Paginator</span>
      </div>
    </div>
  </div>

  <div class="footer-social">
    <h4 style="left:158px">Mural feed</h4>
    <div class="feed-grid" role="img" aria-label="Grid of follower profile photos">
      <div class="thumb"></div><div class="thumb"></div><div class="thumb"></div><div class="thumb"></div>
      <div class="thumb"></div><div class="thumb"></div><div class="thumb"></div><div class="thumb"></div>
      <small>mural page</small>
    </div>
    <h4 style="left:480px">Trillo Updates</h4>
    <div class="tweet-dot"></div>
    <div class="tweet-bubble">@studiotemas there is a new designer in town people!<br><br>Check it out: http://lnk.qv</div>
    <h4 style="left:769px">Follow us</h4>
    <ul class="follow-list">
      <li><span class="sq-chirp"></span>On Trillo</li>
      <li><span class="sq-rss"></span>As RSS Feed</li>
      <li><span class="sq-mural"></span>Shared on Mural</li>
      <li><span class="sq-orbe"></span>On Orbe +</li>
    </ul>
  </div>

  <div class="copyright">© 2013. www.lumarinovo.com | Terms and Conditions | Privacy Statement | Imprint | Glossory</div>
</footer>

</body>
</html>
```